Stationery Design Project for Nimbora, Chicago

Nimbora, a street parking application which helps car drivers find a street parking spot by offering an ideal path along which to look for parking. This path is calculated by our algorithm based on data (e.g. historical data, baseball games schedule, etc.). Along this path the driver will find a spot and will also save 70% of the search time. Customer we target is reg. between 21 and 45 yo.

We envision something young, fresh, bright and original. Slightly abstract maybe. It should represent the idea and elements of finding street parking in the city, e.g. car(s), parking spot, people, city, etc. (just ideas!).

Logo is attached.

Requirement:
- Business Cards (2 Sided Full Color CMYK)
- Letterhead (1 Sided Full Color CMYK)
- Envelope (1 Sided Full Color CMYK)
- Sticker (1 Sided Full Color CMYK), round with a 2inch diameter.

Reason: We're starting to get more and more designs and need more time to look into all of them. Very exciting!! Thanks to everybody!

Hi all, we're in the process of selecting our favs. Though choices!!! Really good submissions. Will keep you posted and sorry for the delay.

Target Market(s)

Car drivers and owners between 21 and 45

Industry/Entity Type

Parking

Requirements
Must have
• Sticker should be round and include company URL nimbora.com and the new logo which we will attach soon.
Should not have
• Should not be too serious or boring.

```html
<!DOCTYPE html>
<html lang="en">
<head>
<meta charset="utf-8">
<title>Nimbora Business Card</title>
<link rel="stylesheet" href="https://fonts.googleapis.com/css2?family=Open+Sans:wght@400;600;700&display=swap">
<style>
  :root {
    --backdrop: #d9d9d9;
    --card-white: #ffffff;
    --ink: #111111;
    --band-dark: #050505;
    --band-mid: #2a2a2a;
    --rule-grey: #6b6b6b;
    --brand-blue: #1f4fd6;
    --brand-blue-deep: #0b1f8a;
    --brand-blue-light: #5aa2ff;
    --back-glow: #7a7a7a;
    --back-dark: #000000;
    --text-light: #ffffff;
  }
  * { margin: 0; padding: 0; box-sizing: border-box; }
  html, body {
    width: 954px;
    height: 1200px;
    overflow: hidden;
    background: var(--backdrop);
    font-family: "Open Sans", Arial, sans-serif;
  }
  .card {
    position: absolute;
    left: 80px;
    width: 796px;
    height: 454px;
    border-radius: 30px;
    overflow: hidden;
    box-shadow: 0 6px 14px rgba(0,0,0,0.35);
  }
  /* Front */
  .card--front { top: 96px; background: var(--card-white); }
  .front__band {
    position: absolute; left: 0; top: 0; width: 100%; height: 76px;
    background: linear-gradient(90deg, var(--band-dark) 0%, var(--band-mid) 50%, var(--band-dark) 100%);
    color: var(--text-light);
    text-align: center;
    line-height: 88px;
  }
  .front__name { font-weight: 700; font-size: 22px; }
  .front__designation { font-weight: 700; font-size: 17px; }
  .front__rule {
    position: absolute; left: 0; top: 80px; width: 100%; height: 8px;
    background: linear-gradient(90deg, #3a3a3a, var(--rule-grey), #3a3a3a);
  }
  .brand-mark {
    position: absolute;
    border-radius: 50%;
    background: radial-gradient(circle at 40% 30%, var(--brand-blue-light) 0%, var(--brand-blue) 45%, var(--brand-blue-deep) 100%);
  }
  .front__mark { left: 134px; top: 142px; width: 150px; height: 150px; box-shadow: 0 0 0 8px #f1f1f1, 0 4px 14px rgba(0,0,0,0.25); }
  .brand-name {
    position: absolute;
    font-weight: 600;
    letter-spacing: 1px;
    line-height: 1;
  }
  .front__brand { left: 312px; top: 162px; font-size: 98px; color: var(--ink); }
  .front__contact {
    position: absolute; left: 0; top: 340px; width: 100%;
    text-align: center; color: var(--ink);
    font-size: 19px; line-height: 32px;
  }
  .front__contact b { font-weight: 700; }
  /* Back */
  .card--back {
    top: 660px;
    background: radial-gradient(ellipse 360px 260px at 450px 220px, var(--back-glow) 0%, #2b2b2b 55%, var(--back-dark) 100%);
  }
  .back__mark { left: 107px; top: 130px; width: 166px; height: 166px; box-shadow: 0 4px 16px rgba(0,0,0,0.6); }
  .back__brand { left: 302px; top: 148px; font-size: 110px; color: var(--text-light); }
</style>
</head>
<body>
  <section class="card card--front">
    <header class="front__band">
      <span class="front__name">Your Name - </span><span class="front__designation">Designation</span>
    </header>
    <div class="front__rule"></div>
    <div class="brand-mark front__mark"></div>
    <div class="brand-name front__brand">Nimbora</div>
    <address class="front__contact" style="font-style:normal">
      <div><b>p</b> : 123-456-7890 &nbsp;|&nbsp; <b>c</b> : 123-456-7890</div>
      <div><b>e</b> : name@website.com &nbsp;|&nbsp; <b>w</b> : www.website.com</div>
      <div>City Name, Street Name, State Name, Country Code</div>
    </address>
  </section>

  <section class="card card--back">
    <div class="brand-mark back__mark"></div>
    <div class="brand-name back__brand">Nimbora</div>
  </section>
</body>
</html>
```